Business Card Design For A Renovation Contractor Company

We need a business card for a new company based in Singapore, our company name is "RB Tolvane". We are a renovation contractor that builds designs into reality. We build more of F&B restaurants, retail stores and commercial offices. We work very closely with designers. The final design should communicate to our client that we are a company that you can trust, that will plan and complete your project without giving you a headache. I like my client to remember my company as "RB". The beauty of SIMPLE is important.

Industry/Entity Type

Contractor

Requirements
Nice to have
• Black or Red base

```html
<!DOCTYPE html>
<html lang="en">
<head>
<meta charset="utf-8">
<title>RB Tolvane – Business Cards</title>
<link rel="stylesheet" href="https://fonts.googleapis.com/css2?family=Source+Sans+3:wght@300;400;700&display=swap">
<style>
  :root {
    --backdrop: #ece7df;
    --card-white: #ffffff;
    --brand-red: #d4232b;
    --brand-black: #000000;
    --ink: #3a3a3a;
    --ink-soft: #555555;
    --ghost: #e6e6e6;
    --on-dark: #ffffff;
  }
  * { box-sizing: border-box; margin: 0; padding: 0; }
  html, body {
    width: 1200px;
    height: 714px;
    overflow: hidden;
    background: var(--backdrop);
    font-family: "Source Sans 3", sans-serif;
  }
  .canvas { position: relative; width: 1200px; height: 714px; }

  .card {
    position: absolute;
    width: 546px;
    height: 313px;
    border-radius: 28px;
    overflow: hidden;
  }
  .card--front { left: 36px; top: 29px; background: var(--card-white); border: 1px solid #9a9a9a; }
  .card--red   { left: 611px; top: 33px; background: var(--brand-red); }
  .card--black { left: 328px; top: 364px; background: var(--brand-black); }

  .brand-disc {
    position: absolute;
    width: 294px;
    height: 294px;
    border-radius: 50%;
    left: 256px;
    top: 9px;
  }
  .card--front .brand-disc { left: 262px; top: 6px; background: var(--ghost); opacity: .7; }
  .card--red .brand-disc   { background: var(--brand-black); }
  .card--black .brand-disc { background: var(--brand-red); }

  .holder { position: absolute; left: 27px; top: 50px; }
  .holder__name { font-weight: 700; font-size: 23px; color: #111; line-height: 1; letter-spacing: .2px; }
  .holder__title { font-size: 17px; color: var(--brand-red); margin-top: 6px; line-height: 1; }

  .website {
    position: absolute; left: 27px; top: 267px;
    font-size: 17px; letter-spacing: 3px; color: var(--ink-soft);
  }
  .website__accent { color: var(--brand-red); font-weight: 700; }

  .contact { position: absolute; left: 337px; top: 176px; list-style: none; }
  .contact__item {
    display: flex; align-items: flex-start; gap: 7px;
    font-size: 14.5px; color: var(--ink); line-height: 1.25;
    margin-bottom: 8px;
  }
  .contact__icon { width: 13px; height: 13px; margin-top: 2px; flex: none; fill: var(--brand-red); }

  .wordmark { position: absolute; left: 24px; top: 214px; color: var(--on-dark); display: inline-block; }
  .wordmark__name {
    font-weight: 300; font-size: 44px; line-height: 1; letter-spacing: -.2px;
  }
  .wordmark__tagline {
    font-weight: 400; font-size: 14.5px; letter-spacing: .8px; line-height: 1.2;
    color: var(--on-dark);
    border-top: 1px solid var(--on-dark);
    margin-top: 4px; padding: 1px 8px 0;
  }
</style>
</head>
<body>
<main class="canvas">

  <section class="card card--front" aria-label="Card front with contact details">
    <div class="brand-disc" aria-hidden="true"></div>
    <div class="holder">
      <p class="holder__name">YOUR NAME</p>
      <p class="holder__title">TITLE</p>
    </div>
    <ul class="contact">
      <li class="contact__item">
        <svg class="contact__icon" viewBox="0 0 14 14" aria-hidden="true"><path d="M1 13V5l6-3 6 3v8z M3 6h8v1H3z M3 8.5h8v1H3z M3 11h8v1H3z" fill-rule="evenodd"/></svg>
        <span>Street Name, City Name<br>State Zip Code</span>
      </li>
      <li class="contact__item">
        <svg class="contact__icon" viewBox="0 0 14 14" aria-hidden="true"><path d="M3 1l2.5 3-1.5 1.5c.8 2 2.5 3.7 4.5 4.5L10 8.5l3 2.5-1.8 2C6 12.5 1.5 8 1 2.8z"/></svg>
        <span>123-456-0789</span>
      </li>
      <li class="contact__item">
        <svg class="contact__icon" viewBox="0 0 14 14" aria-hidden="true"><path d="M3.5 0h7a1 1 0 0 1 1 1v12a1 1 0 0 1-1 1h-7a1 1 0 0 1-1-1V1a1 1 0 0 1 1-1zM4.5 2v6h5V2zM5 10h1v1H5zm2 0h1v1H7zm2 0h1v1H9z" fill-rule="evenodd"/></svg>
        <span>123-456-0789</span>
      </li>
      <li class="contact__item">
        <svg class="contact__icon" viewBox="0 0 14 14" aria-hidden="true"><path d="M1 5l6-4 6 4v8H1z M2 5.5l5 3.5 5-3.5" /></svg>
        <span>info@rbtolvane.com</span>
      </li>
    </ul>
    <p class="website">www.<span class="website__accent">rbtolvane</span>.com</p>
  </section>

  <section class="card card--red" aria-label="Card back, red">
    <div class="brand-disc" aria-hidden="true"></div>
    <div class="wordmark">
      <p class="wordmark__name">RB Tolvane</p>
      <p class="wordmark__tagline">planned well, built to last</p>
    </div>
  </section>

  <section class="card card--black" aria-label="Card back, black">
    <div class="brand-disc" aria-hidden="true"></div>
    <div class="wordmark">
      <p class="wordmark__name">RB Tolvane</p>
      <p class="wordmark__tagline">planned well, built to last</p>
    </div>
  </section>

</main>
</body>
</html>
```